Letterhead, stationery and email signature for construction business

I need the letterhead, stationery and email signature designs for a construction business. I want them to have a corporate feel to them.

I've attached the logo for reference.

```html
<!DOCTYPE html>
<html lang="en">
<head>
<meta charset="utf-8">
<title>Halden Build – Stationery Set</title>
<link rel="stylesheet" href="https://fonts.googleapis.com/css2?family=Montserrat:wght@400;600;700&family=Lato:wght@400;700&family=Great+Vibes&display=swap">
<style>
:root{
  --bg:#f1f2f4;
  --paper:#e4e5e8;
  --blue:#2a64b0;
  --blue-deep:#2553a1;
  --brand:#2b59a6;
  --grey-swoosh:#5b5e66;
  --ink:#333539;
  --white:#ffffff;
}
*{margin:0;padding:0;box-sizing:border-box}
html,body{width:1200px;height:889px;overflow:hidden;background:var(--bg)}
.canvas{position:relative;width:1200px;height:889px;font-family:"Lato",sans-serif;color:var(--ink)}
.piece{position:absolute;background:var(--paper);overflow:hidden}
.wave{position:absolute;left:0;bottom:0;width:100%}
.brand{display:flex;align-items:center;gap:4px;font-family:"Montserrat",sans-serif;font-weight:700;color:var(--brand)}
.brand-mark{background:var(--brand);flex:none}
.brand-name{line-height:1}
.brand-name span{display:block}
.brand-name .sub{letter-spacing:.42em}
.contact{font-family:"Montserrat",sans-serif;font-weight:600;color:var(--ink)}
.contact li{list-style:none;display:flex;align-items:center;gap:3px}
.contact svg{fill:var(--brand);flex:none}

/* letterhead */
.letterhead{left:242px;top:110px;width:329px;height:467px}
.letterhead .brand{position:absolute;left:30px;top:24px}
.letterhead .brand-mark{width:26px;height:26px}
.letterhead .brand-name{font-size:15px}
.letterhead .brand-name .sub{font-size:7px;margin-top:2px}
.letterhead .contact{position:absolute;left:224px;top:19px;border-left:1px solid var(--brand);padding-left:3px;font-size:5.2px;line-height:7.8px}
.letterhead .contact svg{width:5px;height:5px}
.letter{position:absolute;left:26px;top:103px;width:278px;font-size:6px;line-height:7.2px}
.letter p{margin-bottom:7px;text-align:justify}
.letter .salutation{font-size:7.5px;font-weight:700;margin:9px 0 8px}
.letter .signature{font-family:"Great Vibes",cursive;font-size:15px;margin-top:6px;color:#222}

/* folder */
.folder{left:628px;top:88px;width:388px;height:489px;background:var(--blue)}
.folder .brand{position:absolute;left:53px;top:211px;gap:10px;color:var(--white)}
.folder .brand-mark{width:62px;height:62px;background:var(--white)}
.folder .brand-name{font-size:43px}
.folder .brand-name .sub{font-size:19px;margin-top:3px;letter-spacing:.55em}

/* email signature */
.signature-strip{left:1042px;top:87px;width:131px;height:499px;background:var(--paper)}
.signature-inner{position:absolute;left:0;top:499px;width:499px;height:131px;transform:rotate(-90deg);transform-origin:top left}
.signature-inner .brand{position:absolute;left:29px;top:14px}
.signature-inner .brand-mark{width:22px;height:22px}
.signature-inner .brand-name{font-size:17px}
.signature-inner .brand-name .sub{font-size:7px;margin-top:1px}
.sig-person{position:absolute;left:155px;top:14px;font-family:"Montserrat",sans-serif;font-size:11px;line-height:17px;padding-left:8px;border-left:1px solid var(--brand)}
.sig-person .name{font-weight:700;color:var(--brand);font-size:12px}
.signature-inner .contact{position:absolute;left:322px;top:14px;font-weight:400;font-size:11px;line-height:18px;padding-left:8px;border-left:1px solid var(--brand)}
.signature-inner .contact svg{width:9px;height:9px}

/* business cards */
.card-front{left:123px;top:615px;width:151px;height:85px}
.card-front .brand{position:absolute;left:11px;top:27px;gap:3px}
.card-front .brand-mark{width:14px;height:14px}
.card-front .brand-name{font-size:10px}
.card-front .brand-name .sub{font-size:4.5px;margin-top:1px}
.card-front .contact{position:absolute;left:85px;top:13px;border-left:1px solid var(--brand);padding-left:4px;font-size:3.3px;line-height:5.2px;height:36px}
.card-front .contact .name{font-weight:700;color:var(--brand);font-size:5px;line-height:6px}
.card-front .contact svg{width:3.5px;height:3.5px}
.card-back{left:123px;top:722px;width:151px;height:87px;background:var(--blue)}
.card-back .brand{position:absolute;left:27px;top:29px;color:var(--white);gap:4px}
.card-back .brand-mark{width:20px;height:20px;background:var(--white)}
.card-back .brand-name{font-size:15px}
.card-back .brand-name .sub{font-size:6px;margin-top:1px}

/* envelopes */
.envelope-front{left:311px;top:626px;width:369px;height:178px}
.envelope-front .brand{position:absolute;left:16px;top:20px}
.envelope-front .brand-mark{width:20px;height:20px}
.envelope-front .brand-name{font-size:14px}
.envelope-front .brand-name .sub{font-size:6px;margin-top:1px}
.envelope-front .contact{position:absolute;left:16px;top:55px;font-size:5.6px;line-height:8.4px}
.envelope-front .contact .addr{margin-bottom:3px}
.envelope-front .contact svg{width:5px;height:5px}
.envelope-back{left:712px;top:626px;width:371px;height:178px}
.envelope-back .flap{position:absolute;left:0;top:0;width:371px;height:54px}
.envelope-back .flap-mark{position:absolute;left:165px;top:8px;width:36px;height:36px;background:var(--white)}
</style>
</head>
<body>
<svg width="0" height="0" style="position:absolute" aria-hidden="true">
  <symbol id="i-phone" viewBox="0 0 10 10"><path d="M2 1h2l1 2.5-1.3 1a6 6 0 0 0 2.8 2.8l1-1.3L10 7v2a1 1 0 0 1-1 1A9 9 0 0 1 0 1a1 1 0 0 1 1-1z"/></symbol>
  <symbol id="i-mail" viewBox="0 0 10 10"><path d="M0 2h10v6H0z M0.6 2.4 5 5.6 9.4 2.4" fill-rule="evenodd"/><path d="M0.8 2.6 5 5.6l4.2-3" fill="none" stroke="#fff" stroke-width=".8"/></symbol>
  <symbol id="i-web" viewBox="0 0 10 10"><circle cx="5" cy="5" r="5"/><path d="M0 5h10M5 0c-2.5 3-2.5 7 0 10M5 0c2.5 3 2.5 7 0 10" stroke="#fff" stroke-width=".7" fill="none"/></symbol>
</svg>

<main class="canvas">

  <!-- Letterhead -->
  <section class="piece letterhead">
    <div class="brand">
      <div class="brand-mark"></div>
      <div class="brand-name"><span>HALDEN</span><span class="sub">BUILD</span></div>
    </div>
    <ul class="contact">
      <li>42-10 Linden St 5,</li>
      <li style="margin-bottom:2px">Ridgewood, NY 11400</li>
      <li><svg><use href="#i-phone"/></svg>555-201-4870</li>
      <li><svg><use href="#i-mail"/></svg>info@haldenbuild.com</li>
      <li><svg><use href="#i-web"/></svg>www.haldenbuild.com</li>
    </ul>
    <article class="letter">
      <p>Feb-03-2022</p>
      <p>Mr, Paul Grant<br>President</p>
      <p>Norbrook Corporation<br>123 Street Name, Suite# 10<br>City, State, 120023</p>
      <p class="salutation">Dear Mr, Paul</p>
      <p>Lorem ipsum dolor sit amet, consectetur adipisicing elit, sed do eiusmod tempor incididunt ut labore et dolore magna aliqua. Ut enim ad minim veniam, quis nostrud exercitation ullamco laboris nisi ut aliquip ex ea commodo consequat. Duis aute irure dolor in reprehenderit in voluptate velit esse cillum dolore eu fugiat nulla pariatur.</p>
      <p>Lorem ipsum dolor sit amet, consectetur adipisicing elit, sed do eiusmod tempor incididunt ut labore et dolore magna aliqua. Ut enim ad minim veniam, quis nostrud exercitation ullamco laboris nisi ut aliquip ex ea commodo consequat. Duis aute irure dolor in reprehenderit in voluptate velit esse cillum dolore eu fugiat nulla pariatur.</p>
      <p>Lorem ipsum dolor sit amet, consectetur adipisicing elit, sed do eiusmod tempor incididunt ut labore et dolore magna aliqua. Ut enim ad minim veniam, quis nostrud exercitation ullamco laboris nisi ut aliquip ex ea commodo consequat.</p>
      <p>Excepteur sint occaecat cupidatat non proident, sunt in culpa qui officia deserunt mollit anim id est laborum. re et dolore magnam aliquam quaerat voluptatem.</p>
      <p style="margin-top:14px">Regards</p>
      <p class="signature">Daniel Reyes</p>
    </article>
    <svg class="wave" style="height:66px" viewBox="0 0 600 120" preserveAspectRatio="none" aria-hidden="true">
      <path d="M0 4C100 52 200 92 300 94C200 100 90 82 0 44Z" fill="var(--grey-swoosh)"/>
      <path d="M0 52C90 82 180 106 290 98C380 88 420 30 510 34C560 37 590 52 600 58V120H0Z" fill="var(--blue)"/>
    </svg>
  </section>

  <!-- Folder -->
  <section class="piece folder">
    <div class="brand">
      <div class="brand-mark"></div>
      <div class="brand-name"><span>HALDEN</span><span class="sub">BUILD</span></div>
    </div>
  </section>

  <!-- Email signature -->
  <section class="piece signature-strip">
    <div class="signature-inner">
      <div class="brand">
        <div class="brand-mark"></div>
        <div class="brand-name"><span>HALDEN</span><span class="sub">BUILD</span></div>
      </div>
      <div class="sig-person">
        <div class="name">OWEN PARKER</div>
        <div>Managing Director</div>
        <div>Suite 4B Oakmont IL 60</div>
      </div>
      <ul class="contact">
        <li><svg><use href="#i-phone"/></svg>555-318-2264</li>
        <li><svg><use href="#i-mail"/></svg>info@mailhost.com</li>
        <li><svg><use href="#i-web"/></svg>www.sitehost.com</li>
      </ul>
      <svg class="wave" style="height:70px" viewBox="0 0 499 70" preserveAspectRatio="none" aria-hidden="true">
        <path d="M0 10C80 20 160 58 260 60C340 62 420 42 499 36V40C420 46 340 66 260 66C160 64 80 30 0 22Z" fill="var(--grey-swoosh)"/>
        <path d="M0 24C80 32 160 64 260 66C340 67 420 48 499 42V70H0Z" fill="var(--blue-deep)"/>
      </svg>
    </div>
  </section>

  <!-- Business card front -->
  <section class="piece card-front">
    <div class="brand">
      <div class="brand-mark"></div>
      <div class="brand-name"><span>HALDEN</span><span class="sub">BUILD</span></div>
    </div>
    <ul class="contact">
      <li class="name">ELLA MORGAN</li>
      <li style="font-weight:400;margin-bottom:1px">Co-Founder</li>
      <li>42-10 Linden St 5,</li>
      <li style="margin-bottom:1px">Ridgewood, NY 11400</li>
      <li><svg><use href="#i-phone"/></svg>555-201-4870</li>
      <li><svg><use href="#i-mail"/></svg>info@haldenbuild.com</li>
      <li><svg><use href="#i-web"/></svg>www.haldenbuild.com</li>
    </ul>
    <svg class="wave" style="height:24px" viewBox="0 0 600 120" preserveAspectRatio="none" aria-hidden="true">
      <path d="M0 4C100 52 200 92 300 94C200 100 90 82 0 44Z" fill="var(--grey-swoosh)"/>
      <path d="M0 52C90 82 180 106 290 98C380 88 420 30 510 34C560 37 590 52 600 58V120H0Z" fill="var(--blue)"/>
    </svg>
  </section>

  <!-- Business card back -->
  <section class="piece card-back">
    <div class="brand">
      <div class="brand-mark"></div>
      <div class="brand-name"><span>HALDEN</span><span class="sub">BUILD</span></div>
    </div>
  </section>

  <!-- Envelope front -->
  <section class="piece envelope-front">
    <div class="brand">
      <div class="brand-mark"></div>
      <div class="brand-name"><span>HALDEN</span><span class="sub">BUILD</span></div>
    </div>
    <ul class="contact">
      <li>42-10 Linden St 5,</li>
      <li class="addr">Ridgewood, NY 11400</li>
      <li><svg><use href="#i-phone"/></svg>555-201-4870</li>
      <li><svg><use href="#i-mail"/></svg>info@haldenbuild.com</li>
      <li><svg><use href="#i-web"/></svg>www.haldenbuild.com</li>
    </ul>
    <svg class="wave" style="height:75px" viewBox="0 0 600 120" preserveAspectRatio="none" aria-hidden="true">
      <path d="M0 4C100 52 200 92 300 94C200 100 90 82 0 44Z" fill="var(--grey-swoosh)"/>
      <path d="M0 52C90 82 180 106 290 98C380 88 420 30 510 34C560 37 590 52 600 58V120H0Z" fill="var(--blue)"/>
    </svg>
  </section>

  <!-- Envelope back -->
  <section class="piece envelope-back">
    <svg class="flap" viewBox="0 0 371 54" preserveAspectRatio="none" aria-hidden="true">
      <path d="M0 0H371L355 40Q350 53 335 53H36Q21 53 16 40Z" fill="var(--blue)"/>
    </svg>
    <div class="flap-mark"></div>
  </section>

</main>
</body>
</html>
```